Website Design for The Elder Nook

Please design and code a new website.
Here are the sites I like best:
http://www.voyaglint.com/alternate/
http://www.wheelgiftbay.org
Please make it similar but look at the competitor site (below) for images and wording. This is NOT a car donation site. It's a senior lead placement site like https://www.kinhavenfinder.com. I just like this sites above as a lead generation sites.
Competitor site:
https://www.kinhavenfinder.com (use ideas / verbiage from this site)
Updates
Competitor site:
Coding
Coded - Design and coding required
Number of Pages Required
1 page
Look and feel
Each slider illustrates characteristics of the customer's brand and the style your logo design should communicate.

```html
<!DOCTYPE html>
<html lang="en">
<head>
<meta charset="utf-8">
<title>The Elder Nook – Find Senior Living Near You</title>
<link href="https://fonts.googleapis.com/css2?family=Lato:wght@400;700;900&display=swap" rel="stylesheet">
<style>
:root{
  --orange:#ff7a00;
  --dark:#222222;
  --darker:#1b1b1b;
  --footer:#3a3a3a;
  --text:#333333;
  --muted:#555555;
  --card:#efefef;
  --white:#ffffff;
}
*{box-sizing:border-box;margin:0;padding:0}
html,body{width:1200px;height:3112px;overflow:hidden;background:var(--white);font-family:'Lato',sans-serif;color:var(--text)}
.page{position:absolute;left:60px;top:0;width:1081px}
section,header,nav,footer{position:relative;width:100%}
.site-header{height:101px}
.brand{position:absolute;left:16px;top:24px;font-size:42px;font-weight:700;color:#444}
.call{position:absolute;right:16px;top:26px;display:flex;align-items:center;gap:16px}
.call-label{font-size:14px;font-weight:700;color:#333;letter-spacing:.3px}
.call-number{font-size:34px;font-weight:700;color:var(--orange);line-height:1.05}
.main-nav{height:51px;background:var(--dark);display:flex;justify-content:space-around;align-items:center;padding:0 20px}
.main-nav a{color:var(--white);font-size:14px;font-weight:700;text-decoration:none}
.hero{height:509px;display:flex}
.hero-search{width:527px;background:var(--orange);color:var(--white);text-align:center;padding-top:96px}
.hero-search h1{font-size:33px;font-weight:700;line-height:1.1}
.hero-search h2{font-size:23px;font-weight:700;margin-top:8px}
.field{display:block;margin:0 auto;width:335px;height:44px;background:var(--white);color:#444;font-size:17px;line-height:44px;border:none}
.hero-search .field{margin-top:26px}
.btn-dark{display:block;margin:10px auto 0;width:335px;height:44px;background:var(--dark);color:var(--white);font-size:21px;font-weight:700;line-height:44px;border-radius:2px}
.help{font-size:24px;font-weight:700;margin-top:26px}
.help-number{font-size:33px;font-weight:700}
.hero-photo{flex:1;background:linear-gradient(135deg,#8c9a52 0%,#c9c08c 45%,#e8dccb 75%,#f2ede6 100%)}
.support{height:424px;text-align:center}
.section-title{font-size:30px;font-weight:700}
.support .section-title{padding-top:50px}
.support p{font-size:16.5px;color:var(--muted);line-height:27px;width:820px;margin:16px auto 0}
.features{display:flex;gap:32px;padding:0 14px;margin-top:40px}
.feature{width:240px;height:200px;background:var(--card);padding-top:23px;font-size:19px;color:#444;line-height:22px}
.icon-circle{width:90px;height:90px;border-radius:50%;background:var(--orange);margin:0 auto 20px;display:flex;align-items:center;justify-content:center}
.dark{background:var(--darker);color:var(--white);text-align:center}
.advisor{height:420px}
.advisor .section-title{padding-top:44px}
.advisor .lead{font-size:19px;margin-top:18px}
.benefits{display:flex;justify-content:space-around;padding:0 100px;margin-top:42px}
.benefit{width:260px;font-size:19px;font-weight:700;line-height:26px}
.benefit svg{display:block;margin:0 auto 10px;height:52px}
.advisor-form{display:flex;justify-content:center;gap:11px;margin-top:48px}
.advisor-form .field{margin:0;width:425px;height:48px;line-height:48px;text-align:left;padding-left:16px;font-size:14px}
.btn-orange{background:var(--orange);color:var(--white);font-weight:700;text-align:center;display:inline-block}
.advisor-form .btn-orange{width:256px;height:48px;line-height:48px;font-size:15px}
.veterans{height:449px}
.portrait{position:absolute;left:68px;top:50px;width:338px;height:338px;border-radius:50%;background:radial-gradient(circle at 50% 45%,#e8e4df 0%,#aab09a 45%,#4d5a3c 100%)}
.vet-copy{position:absolute;left:464px;top:52px;width:560px}
.vet-copy h2{font-size:30px;font-weight:700;line-height:36px}
.vet-copy p{font-size:14px;color:var(--muted);line-height:26px;margin-top:18px}
.vet-copy .btn-orange{width:152px;height:45px;line-height:45px;font-size:15px;margin-top:30px}
.testimonials{height:560px}
.testimonials .section-title{padding-top:42px;font-weight:700}
.quotes{display:flex;justify-content:space-around;padding:0 60px;margin-top:30px}
.quote{width:280px;font-size:18px;font-weight:700;line-height:26px}
.avatar{width:158px;height:158px;border-radius:50%;margin:0 auto 22px;background:radial-gradient(circle at 50% 40%,#eadfd6 0%,#c7b8a8 50%,#7c8a96 100%)}
.quote .name{color:var(--orange);margin-top:16px}
.testimonials .btn-orange{width:334px;height:52px;line-height:52px;font-size:17px;margin-top:34px}
.states{height:305px;text-align:center}
.states .section-title{padding-top:48px}
.state-list{display:flex;justify-content:space-around;padding:0 20px;margin-top:30px}
.state{width:190px;font-size:20px;color:#333}
.state-icon{width:76px;height:80px;margin:0 auto 22px;background:var(--orange);border-radius:14px}
.site-footer{height:293px;background:var(--footer);color:var(--white)}
.col{position:absolute;top:34px}
.col h3{font-size:22px;font-weight:400}
.about{left:16px;width:340px}
.about p{font-size:13px;line-height:24px;margin-top:14px}
.about .btn-orange{width:168px;height:38px;line-height:38px;font-size:14px;margin-top:28px}
.resources{left:457px}
.resources ul{list-style:none;margin-top:10px}
.resources li{font-size:13px;line-height:30px}
.social{left:735px}
.social-icons{display:flex;gap:18px;margin-top:14px}
.social-icons span{width:20px;height:20px;border-radius:50%;background:var(--white)}
.badges{display:flex;gap:14px;margin-top:40px}
.badge{height:44px;background:#cfd6e4;border:2px solid #fff}
.copyright{font-size:12px;margin-top:42px}
</style>
</head>
<body>
<div class="page">
  <header class="site-header">
    <div class="brand">The Elder Nook</div>
    <div class="call">
      <svg width="26" height="26" viewBox="0 0 24 24" aria-hidden="true"><path fill="#333" d="M6.6 10.8a15.1 15.1 0 0 0 6.6 6.6l2.2-2.2c.3-.3.7-.4 1-.2 1.1.4 2.3.6 3.6.6.6 0 1 .4 1 1V20c0 .6-.4 1-1 1A17 17 0 0 1 3 4c0-.6.4-1 1-1h3.5c.6 0 1 .4 1 1 0 1.3.2 2.5.6 3.6.1.3 0 .7-.2 1z"/></svg>
      <div><div class="call-label">CALL US TODAY</div><div class="call-number">1-800-555-0142</div></div>
    </div>
  </header>

  <nav class="main-nav">
    <a>ASSISTED LIVING</a><a>MEMORY CARE</a><a>NURSING HOMES</a><a>MORE LIVING OPTIONS</a><a>PLANNING &amp; ADVICE</a><a>HOW OUR SERVICE WORKS</a>
  </nav>

  <section class="hero">
    <div class="hero-search">
      <h1>You know your family.<br>We know SENIOR LIVING.</h1>
      <h2>Find Senior Living Near You.</h2>
      <div class="field">Enter city or postal code</div>
      <div class="btn-dark">Start Your Search</div>
      <div class="help">Need help?</div>
      <div class="help-number">1-800-555-0142</div>
    </div>
    <div class="hero-photo" role="img" aria-label="Photo of a smiling senior couple sitting together on a sofa"></div>
  </section>

  <section class="support">
    <h2 class="section-title">The support you need to make the Right Choice</h2>
    <p>Lorem ipsum dolor sit amet, consectetur adipiscing elit. Morbi vel suscipit diam, ut finibus arcususpendisse facilisis vitae erat ac scelerisque.</p>
    <div class="features">
      <div class="feature"><div class="icon-circle"><svg width="40" height="40" viewBox="0 0 24 24"><circle cx="12" cy="7" r="5" fill="#fff"/><path fill="#fff" d="M2 22c0-6 4-9 10-9s10 3 10 9z"/></svg></div>Dedicated local<br>advisor</div>
      <div class="feature"><div class="icon-circle"><svg width="44" height="40" viewBox="0 0 26 24"><path fill="none" stroke="#fff" stroke-width="2.6" d="M1 3h4l3 12h14l3-9H7"/><circle cx="10" cy="20" r="2.2" fill="#fff"/><circle cx="20" cy="20" r="2.2" fill="#fff"/><path fill="#fff" d="M8 7h16l-2.5 7H10z"/></svg></div>Full details and<br>pricing</div>
      <div class="feature"><div class="icon-circle"><svg width="42" height="42" viewBox="0 0 24 24"><rect x="2" y="4" width="20" height="18" rx="2" fill="none" stroke="#fff" stroke-width="2"/><rect x="2" y="4" width="20" height="5" fill="#fff"/><path stroke="#fff" stroke-width="1.4" d="M7 9v13M12 9v13M17 9v13M2 13.5h20M2 18h20"/><path stroke="#fff" stroke-width="2" d="M7 2v4M17 2v4"/></svg></div>Help scheduling<br>tours</div>
      <div class="feature"><div class="icon-circle"><svg width="46" height="40" viewBox="0 0 28 24"><ellipse cx="11" cy="9" rx="10" ry="7" fill="#fff"/><path fill="#fff" d="M4 14l-2 5 6-3z"/><ellipse cx="18" cy="14" rx="9" ry="6.5" fill="#fff" stroke="#ff7a00" stroke-width="1.6"/><path fill="#fff" d="M24 18l3 4-7-2z"/></svg></div>Move<br>in support</div>
    </div>
  </section>

  <section class="advisor dark">
    <h2 class="section-title">Your LOCAL ADVISOR informs. You decide.</h2>
    <p class="lead">Over 400 senior advisors across the U.S. and Canada are ready to help your family with:</p>
    <div class="benefits">
      <div class="benefit"><svg viewBox="0 0 24 34" width="36"><path fill="#ff7a00" d="M12 0A12 12 0 0 0 0 12c0 9 12 22 12 22s12-13 12-22A12 12 0 0 0 12 0z"/><circle cx="12" cy="12" r="4.5" fill="#1b1b1b"/></svg>Insider's tips for the area<br>near you</div>
      <div class="benefit"><svg viewBox="0 0 24 21" width="58"><path fill="#fff" d="M12 21 2 11A6 6 0 0 1 12 3a6 6 0 0 1 10 8z"/></svg>Advice tailored to your<br>unique situation</div>
      <div class="benefit"><svg viewBox="0 0 24 24" width="50"><circle cx="12" cy="12" r="10" fill="none" stroke="#fff" stroke-width="2.6"/><path fill="none" stroke="#fff" stroke-width="2.6" d="M12 6v7H7"/></svg>Time saving know-how and<br>resources</div>
    </div>
    <div class="advisor-form">
      <div class="field">Enter City or postal code</div>
      <div class="btn-orange">FIND AN ADVISOR NEAR YOU</div>
    </div>
  </section>

  <section class="veterans">
    <div class="portrait" role="img" aria-label="Portrait photo of an elderly veteran outdoors in a park"></div>
    <div class="vet-copy">
      <h2>Access up to $2,000 per month<br>in veteran's aid</h2>
      <p>Lorem ipsum dolor sit amet, consectetur adipiscing elit. Morbi vel suscipit diam, ut finibus arcu. Suspendisse facilisis vitae erat ac scelerisque. Sed quam diam, feugiat ac pharetra a, commodo quis ante. Aenean sit amet bibendum est, vel finibus lorem. Nulla ut dolor sapien</p>
      <div class="btn-orange">READ MORE</div>
    </div>
  </section>

  <section class="testimonials dark">
    <h2 class="section-title">What Our Customer Says</h2>
    <div class="quotes">
      <div class="quote"><div class="avatar" role="img" aria-label="Customer portrait photo of a senior woman"></div>“ Nulla vitae ante metusa enean et justo lorem. In vestibulum velit quam, sed aliquam nulla varius vitae..”<div class="name">Name Heading</div></div>
      <div class="quote"><div class="avatar" role="img" aria-label="Customer portrait photo of a senior man"></div>“ Nulla vitae ante metusa enean et justo lorem. In vestibulum velit quam, sed aliquam nulla varius vitae..”<div class="name">Name Heading</div></div>
      <div class="quote"><div class="avatar" role="img" aria-label="Customer portrait photo of a smiling senior man"></div>“ Nulla vitae ante metusa enean et justo lorem. In vestibulum velit quam, sed aliquam nulla varius vitae..”<div class="name">Name Heading</div></div>
    </div>
    <div class="btn-orange">SEE MORE TESTIMONIALS</div>
  </section>

  <section class="states">
    <h2 class="section-title">Senior Living by State</h2>
    <div class="state-list">
      <div class="state"><div class="state-icon" role="img" aria-label="Illustration of a caregiver helping a senior walk"></div>Assisted Living</div>
      <div class="state"><div class="state-icon" role="img" aria-label="Illustration of a head in profile"></div>Memory Care</div>
      <div class="state"><div class="state-icon" role="img" aria-label="Illustration of an independent person with raised arms"></div>Independent Living</div>
      <div class="state"><div class="state-icon" role="img" aria-label="Illustration of a nurse with a wheelchair user"></div>Nursing Home</div>
      <div class="state"><div class="state-icon" role="img" aria-label="Illustration of hands holding a house"></div>Care Homes</div>
    </div>
  </section>

  <footer class="site-footer">
    <div class="col about">
      <h3>About Our Company</h3>
      <p>Lorem ipsum dolor sit amet, consectetur adipiscing elit. Morbi vel suscipit diam, ut finibus arcu. Suspendisse facilisis vitae erat ac scelerisque vitae risus facilisis, lacinia libero..</p>
      <div class="btn-orange">Find Out More</div>
    </div>
    <div class="col resources">
      <h3>Resources</h3>
      <ul><li>Aenean et justo lorem</li><li>Estibulum velit quam</li><li>Sed aliquam</li><li>Donec ut lectus egestas</li><li>Convallis ipsum</li></ul>
    </div>
    <div class="col social">
      <h3>Stay In Touch</h3>
      <div class="social-icons"><span></span><span></span><span></span><span></span><span></span></div>
      <div class="badges"><div class="badge" style="width:140px"></div><div class="badge" style="width:92px"></div></div>
      <p class="copyright">Copyright © 2019. Company Name.  All Right Reserved</p>
    </div>
  </footer>
</div>
</body>
</html>
```